Hull Harbour Trade Website makeover

Hull Harbour Trade is in need of a makeover. It is feeling tired and needs a fresh new look and feel as well as being user friendly.

Hull Harbour Trade is an industry owned marketplace website for the sale of recreational boats, marina berths, chandlery, water craft like kayaks - anything related to recreation on the water. The main focus however is boats - new and used. The site is only available to industry businesses so no private sales are available on the site.

This approach ensures that the buyers know that title is guaranteed to all boats sold and that the businesses are reputable and stand behind their products.

The current site address is www.hullharbourtrade.com.au

Target Market(s)

The target market are people interested in outdoor recreation - boaters, kayakers, sailors, paddle boarders, those looking for marina berths for their boat and those looking for service providers.

It should appeal to families, males and females, sports oriented people, fishermen, and those just looking for a relaxing, outdoor, healthy lifestyle.

Requirements
Must have
• Be very user friendly, intuitive in terms of searching, be uncluttered, fresh and engaging.
• Marine recreation is about lifestyle, fun and relaxation. When people buy a boat they are buying into a desirable, healthy lifestyle.
• It must present as professional and give consumers confidence about the professionalism of the businesses selling their products on the site.
Nice to have
• Good images that portray the lifestyle in the Australian marketplace.
• Cater for the needs of sellers to be able to showcase their products to consumers.
Should not have
• Be cluttered and hard to navigate.

```html
<!DOCTYPE html>
<html lang="en">
<head>
<meta charset="utf-8">
<title>Hull Harbour Trade</title>
<link href="https://fonts.googleapis.com/css2?family=Open+Sans:wght@400;600&family=Source+Sans+3:wght@400;600&display=swap" rel="stylesheet">
<style>
:root{
  --navy:#0a2f7a;
  --blue:#0d5fa8;
  --blue-mid:#1a73c2;
  --sky:#7fb6e6;
  --ink:#16386e;
  --text:#5a5f66;
  --page:#eef3f8;
  --line:#d6dde5;
  --white:#fff;
}
*{box-sizing:border-box;margin:0;padding:0}
html,body{width:914px;height:1200px;overflow:hidden}
body{position:relative;font-family:"Open Sans",Arial,sans-serif;background:var(--page);color:var(--text)}
.backdrop{position:absolute;left:0;top:0;width:914px;height:370px;background:linear-gradient(180deg,#cfe2f3 0%,#8ec0e8 18%,#3a8ccc 40%,#2a78bf 60%,#a9cdeb 85%,var(--page) 100%)}
.abs{position:absolute}
.top-links{right:72px;top:13px;font-size:10px;color:var(--blue)}
.top-links span{color:#6a8fb8;margin:0 4px}
.brand{left:70px;top:28px;display:flex;align-items:center;gap:8px;font-family:"Source Sans 3",sans-serif;font-weight:600;font-size:24px;color:var(--navy);line-height:1}
.brand i{display:block;width:22px;height:22px;background:var(--navy)}
.call{right:72px;top:54px;text-align:right;font-family:"Source Sans 3",sans-serif;color:var(--ink)}
.call small{display:block;font-size:14px}
.call strong{display:block;font-size:20px;font-weight:600;color:var(--navy);margin-top:-2px}
.nav{left:68px;top:100px;width:778px;height:40px;background:linear-gradient(#1676c4,#0b5aa3);display:flex;border-radius:2px 2px 0 0}
.nav a{color:#fff;text-decoration:none;font-family:"Source Sans 3",sans-serif;font-size:13px;display:flex;align-items:center;padding:0 12px;border-right:1px solid #0a4d8e;flex:auto;justify-content:center}
.nav a:last-child{border:0}
.hero{left:68px;top:141px;width:779px;height:307px;background:#fff;padding:3px;box-shadow:0 3px 8px rgba(0,0,0,.15)}
.hero-photo{width:100%;height:100%;background:linear-gradient(180deg,#6e7d78 0%,#8b8f80 14%,#3d6e9b 18%,#2b5f92 60%,#5a86b2 80%,#3c668f 100%);position:relative}
.caption{position:absolute;left:0;top:164px;width:370px;height:79px;background:linear-gradient(90deg,rgba(120,175,225,.95),rgba(150,195,235,.9));clip-path:polygon(0 0,100% 0,88% 100%,0 100%);padding:14px 0 0 26px;color:#fff;font-family:"Source Sans 3",sans-serif}
.caption h2{font-weight:400;font-size:23px;line-height:1.1}
.caption p{font-size:14px}
.dots{position:absolute;left:368px;top:284px;display:flex;gap:3px}
.dots b{width:9px;height:9px;border-radius:50%;background:#fff}
.search{left:68px;top:470px;width:539px;height:230px;background:#fff;border:1px solid var(--line);border-radius:3px;padding:18px 23px}
.search h1{font-family:"Source Sans 3",sans-serif;font-weight:400;font-size:23px;color:var(--navy)}
.field{position:absolute;height:25px;border:1px solid #cfd5db;background:linear-gradient(#f2f4f6,#fafbfc);border-radius:2px}
.select{font-size:10px;color:#444;padding:5px 10px}
.select svg{position:absolute;right:8px;top:10px}
.btn{position:absolute;height:26px;border-radius:3px;color:#fff;font-size:11.5px;display:flex;align-items:center;justify-content:center}
.btn.dark{background:linear-gradient(#0d3e8e,#072c6a)}
.btn.light{background:#9ecbee}
.hint{position:absolute;left:23px;top:88px;font-size:11px;color:var(--blue)}
.states{position:absolute;left:25px;top:113px;display:flex;gap:8px;font-size:9.5px;color:#777;align-items:center}
.states span{display:flex;align-items:center;gap:4px}
.states i{display:inline-block;width:13px;height:13px;border:1px solid #c8ced4;border-radius:2px;background:#f5f6f7}
.states .radio{border-radius:50%;width:11px;height:11px}
.states .radio+em{margin-right:6px}
.states em{font-style:normal}
.lbl{position:absolute;top:155px;font-size:10px;color:var(--ink)}
.adv{position:absolute;right:27px;top:201px;font-size:10px;color:var(--blue);text-decoration:underline}
.promo{left:621px;top:471px;width:225px;height:229px;background:linear-gradient(#0c5aa6,#063a85);padding:20px;color:#fff}
.promo h3{font-family:"Source Sans 3",sans-serif;font-weight:400;font-size:23px;line-height:1.1}
.promo h4{font-size:11px;font-weight:600;margin:12px 0 6px}
.promo p{font-size:9px;line-height:1.85}
.promo .cta{position:absolute;left:20px;top:175px;width:188px;height:29px;border-radius:3px;background:#4e97d8;font-size:10.5px;display:flex;align-items:center;justify-content:center}
.latest{left:620px;top:711px;width:225px;height:287px;background:#fff;border:1px solid var(--line);border-radius:3px;overflow:hidden}
.latest h3{font-family:"Source Sans 3",sans-serif;font-weight:400;font-size:17px;color:#3a3f46;background:linear-gradient(#f6f7f8,#eceff2);height:37px;padding:8px 21px;border-bottom:1px solid var(--line)}
.item{padding:11px 0 0 21px}
.item h5{font-size:11px;font-weight:600;color:var(--navy)}
.item p{font-size:9px;color:#8a8f95;line-height:1.85;margin-top:1px;padding-right:12px}
.item time{font-size:8px;color:var(--navy)}
.about{left:67px;top:726px;width:525px}
.about h2{font-family:"Source Sans 3",sans-serif;font-weight:400;font-size:22px;color:#2b3038;margin-bottom:6px}
.about p{font-size:9.6px;line-height:1.76;margin-bottom:16px}
.about h3{font-size:11.5px;font-weight:400;color:#3a3f46;margin:-4px 0 4px}
.about p.tight{margin-bottom:8px}
.footer{left:0;top:1110px;width:914px;height:90px;background:#e6edf4;border-top:1px solid #d3dce6}
.foot-nav{position:absolute;left:70px;top:22px;font-size:10.5px;color:var(--blue)}
.foot-nav span{margin:0 4px;color:#7a93b0}
.copy{position:absolute;left:70px;top:46px;font-size:8.5px;color:#556}
.social{position:absolute;right:70px;top:21px;display:flex;gap:6px}
.social i{width:19px;height:19px;border-radius:2px;display:block}
</style>
</head>
<body>
<div class="backdrop" role="img" aria-label="Bright sky over open blue sea with a sailing yacht behind the header"></div>

<div class="abs top-links">Usefull links<span>|</span>Contact Us<span>|</span>Hull Harbour Trade Member</div>
<div class="abs brand"><i></i>Hull Harbour Trade</div>
<div class="abs call"><small>Call Us Today</small><strong>07 3000 4182</strong></div>

<nav class="abs nav">
  <a>HOME</a><a>ABOUT US</a><a>BOAT FOR SALE</a><a>NEW BOATS</a><a>MARINE ACCESSORIS</a><a>PRODUCT</a><a>SERVICES</a><a>BROKER &amp; DEALERS</a>
</nav>

<section class="abs hero">
  <div class="hero-photo" role="img" aria-label="Large white motor yacht cruising at speed along a rocky coastline">
    <div class="caption"><h2>Duis tincidunt lectus quis viverra</h2><p>Mauris vel lacus vitae felis vestibulum</p></div>
    <div class="dots"><b></b><b></b><b></b><b></b></div>
  </div>
</section>

<section class="abs search">
  <h1>New and Used Boats for Sale</h1>
  <div class="field" style="left:23px;top:50px;width:238px"></div>
  <div class="field select" style="left:268px;top:50px;width:125px">all words<svg width="10" height="6"><path d="M0 0h10L5 6z" fill="#222"/></svg></div>
  <div class="btn dark" style="left:402px;top:50px;width:98px">Quick Search</div>
  <div class="hint">OR Select your state/s, a price range and new/used</div>
  <div class="states">
    <span><i class="radio"></i><em>Select All</em></span>
    <span><i></i>QLD</span><span><i></i>NSW</span><span><i></i>VIC</span><span><i></i>TAS</span><span><i></i>SA</span><span><i></i>NT</span><span><i></i>WA</span>
  </div>
  <div class="lbl" style="left:25px">New and/or Used</div>
  <div class="lbl" style="left:161px">Price from</div>
  <div class="lbl" style="left:280px">Price to</div>
  <div class="field" style="left:25px;top:170px;width:129px"></div>
  <div class="field" style="left:161px;top:170px;width:113px"></div>
  <div class="field" style="left:279px;top:170px;width:113px"></div>
  <div class="btn dark" style="left:402px;top:169px;width:58px">Search</div>
  <div class="btn light" style="left:465px;top:169px;width:50px">Clear</div>
  <div class="adv">Advanced Search</div>
</section>

<aside class="abs promo">
  <h3>Want us to do the searching for you?</h3>
  <h4>Register now!</h4>
  <p>We can email you when boats are listed that match your criteria. We can also alert our members with what you are looking for. Its that easy!</p>
  <div class="cta">REGISTER FOR EMAIL ALERTS</div>
</aside>

<aside class="abs latest">
  <h3>LATEST LISTING</h3>
  <div class="item"><h5>Etiam eu urna</h5><p>Morbi eget arcu Morbi porta libero id ullam-corper nonummy nibh ligula pulvinar</p><time>23 November 2013</time></div>
  <div class="item"><h5>Morbi diam mauri</h5><p>Morbi eget arcu Morbi porta libero id ullam-corper nonummy nibh ligula pulvinar</p><time>23 November 2013</time></div>
  <div class="item"><h5>Donec scelerisque leo</h5><p>Morbi eget arcu Morbi porta libero id ullam-corper nonummy nibh ligula pulvinar</p><time>23 November 2013</time></div>
</aside>

<article class="abs about">
  <h2>Boats for Sale backed by the Marine Trade Council</h2>
  <p>The Marine Trade Councils and their network of members welcome you to the only marine marketplace website offering the largest range of boats for sale and other marine related products, backed by the association quality assurance programs. When you deal with the professionals of the marine industry you are assured of highest possible standard of service and product quality. All marine industry members are bound by the code of conduct and ethics, set down by their Industry Association.</p>
  <p>HullHarbourTrade.com.au is owned and operated by the Marine Trade Councils of Australia and offers the consumer the benefit of making their purchase with the utmost confidence, from expert marine focused members, offering quality products and service.</p>
  <h3>Buy with Confidence</h3>
  <p class="tight">You have come to the right place: HullHarbourTrade.com.au offers all types of boats for sale including fishing boats, power boats, sailing boats, catamarans, trimarans, monohulls, mulithulls, trailer sailers, cruisers, super yachts and boat shares.</p>
  <p>There are new and used boats for sale by Accredited Boat Brokers and Dealers from across Australia. Boat for Sale listings are updated by the seller making Hull Harbour Trade the up-to-date source of information for the boat buyer. With inventory info and lots of photos, Hull Harbour Trade is the best-referenced boat sales site on the net.</p>
</article>

<footer class="abs footer">
  <div class="foot-nav">HOME<span>|</span>ABOUT US<span>|</span>BOAT FOR SALE<span>|</span>NEW BOATS<span>|</span>MARINE ACCESSORIS<span>|</span>PRODUCT<span>|</span>SERVICES<span>|</span>BROKER &amp; DEALERS</div>
  <div class="copy">© 2013 Company Name. All right reserved.&nbsp; Term of Use</div>
  <div class="social">
    <i style="background:#3b5a98"></i><i style="background:#5fb4e6"></i><i style="background:#1672b0"></i><i style="background:#f28b22"></i>
  </div>
</footer>
</body>
</html>
```